iOS7 test prep app

I need 3 basic screens and 2 product images for an iOS7 app I am prototyping. I provided lots of detail in the attached brief. This is an education product, so warm colors (especially reds) work best.

If you've done flat design for mobile products, please take a look ... Thanks!

Greetings, all. Thank you for your submissions. I am meeting with my product development team this week to review your submissions, and will select a designer before the end of the week. I appreciate your patience with my process, and thank you again for your interest in my project. I'll be back to you soon ... -Gerald

```html
<!DOCTYPE html>
<html lang="en">
<head>
<meta charset="utf-8">
<title>Kest Apps – Question Screen</title>
<link rel="stylesheet" href="https://fonts.googleapis.com/css2?family=Open+Sans:wght@600&family=Roboto+Condensed:wght@400;700&display=swap">
<style>
  :root {
    --black: #000000;
    --header-red: #ed1c24;
    --button-red: #c8282d;
    --bar-dark: #151515;
    --accent-green: #1fbf3a;
    --bubble-green: #2a8a35;
    --button-green: #2b8c3a;
    --option-bg: rgba(38, 38, 38, 0.88);
    --option-text: #b9b9b9;
    --white: #ffffff;
    --scene-top: #7b7068;
    --scene-bottom: #4d4843;
  }
  * { box-sizing: border-box; margin: 0; padding: 0; }
  html, body {
    width: 669px; height: 1200px; overflow: hidden;
    background: var(--black);
  }
  .screen {
    position: relative; width: 669px; height: 1200px; overflow: hidden;
    font-family: "Roboto Condensed", "Arial Narrow", sans-serif;
    color: var(--white);
  }
  .status-bar {
    position: absolute; top: 0; left: 0; width: 100%; height: 47px;
    background: var(--black);
    display: flex; align-items: center; justify-content: space-between;
    padding: 0 10px 0 10px; font-family: "Roboto Condensed", sans-serif;
    font-weight: 700; font-size: 25px;
  }
  .status-carrier { display: flex; align-items: center; gap: 4px; width: 200px; }
  .status-time { position: absolute; left: 0; right: 0; text-align: center; pointer-events: none; }
  .status-icons { display: flex; align-items: center; gap: 10px; }
  .app-header {
    position: absolute; top: 47px; left: 0; width: 100%; height: 104px;
    background: var(--header-red);
    display: flex; align-items: center; justify-content: center;
  }
  .app-title { font-size: 50px; font-weight: 400; letter-spacing: -0.5px; }
  .header-back { position: absolute; left: 28px; top: 34px; }
  .header-menu { position: absolute; right: 30px; top: 38px; }
  .question-bar {
    position: absolute; top: 151px; left: 0; width: 100%; height: 105px;
    background: var(--bar-dark);
    display: flex; align-items: center; padding-left: 30px;
    color: var(--accent-green); font-size: 29px;
  }
  .question-next { position: absolute; right: 26px; top: 38px; }
  .content-backdrop {
    position: absolute; top: 256px; left: 0; width: 100%; height: 944px;
    background: linear-gradient(160deg, var(--scene-top) 0%, #6a6058 45%, var(--scene-bottom) 100%);
  }
  .question-badge {
    position: absolute; left: 22px; top: 280px; width: 80px; height: 80px;
    border-radius: 50%; background: var(--bubble-green);
    display: flex; align-items: center; justify-content: center;
    color: var(--black); font-family: "Open Sans", sans-serif; font-size: 56px; font-weight: 600;
  }
  .question-bubble {
    position: absolute; left: 121px; top: 280px; width: 526px; height: 145px;
    background: var(--bubble-green); border-radius: 3px;
    padding: 14px 22px;
    font-family: "Open Sans", sans-serif; font-weight: 600; font-size: 17.4px; line-height: 29.5px;
  }
  .question-bubble::before {
    content: ""; position: absolute; left: -14px; top: 30px;
    border-top: 12px solid transparent; border-bottom: 12px solid transparent;
    border-right: 14px solid var(--bubble-green);
  }
  .answer-list { position: absolute; left: 121px; top: 441px; width: 526px; list-style: none; }
  .answer-option {
    height: 61px; margin-bottom: 17px; background: var(--option-bg); border-radius: 3px;
    display: flex; align-items: center; padding-left: 21px;
    color: var(--option-text); font-size: 20px;
  }
  .action-button {
    position: absolute; left: 194px; width: 381px; height: 57px; border-radius: 2px;
    display: flex; align-items: center; justify-content: center;
    font-size: 25px; color: var(--white);
  }
  .confidence-button { top: 779px; background: var(--button-red); }
  .submit-button { top: 1012px; background: var(--button-green); }
  .confidence-slider { position: absolute; left: 120px; top: 895px; }
</style>
</head>
<body>
<div class="screen">
  <div class="status-bar">
    <div class="status-carrier">
      <svg width="38" height="18" viewBox="0 0 38 18" aria-hidden="true">
        <rect x="0" y="11" width="5" height="7" fill="#fff"/><rect x="7" y="8" width="5" height="10" fill="#fff"/>
        <rect x="14" y="5" width="5" height="13" fill="#fff"/><rect x="21" y="2" width="5" height="16" fill="#fff"/>
        <rect x="28" y="0" width="5" height="18" fill="#fff"/>
      </svg>
      <span>Nova</span>
    </div>
    <div class="status-time">4:20 PM</div>
    <div class="status-icons">
      <svg width="22" height="22" viewBox="0 0 22 22" aria-hidden="true"><circle cx="11" cy="11" r="10" fill="#fff"/><path d="M11 5v6h4" stroke="#000" stroke-width="2.4" fill="none"/></svg>
      <svg width="24" height="24" viewBox="0 0 24 24" aria-hidden="true"><path d="M22 2 2 11l9 2 2 9z" fill="#fff"/></svg>
      <svg width="30" height="30" viewBox="0 0 30 30" aria-hidden="true"><path d="M15 3a12 12 0 1 0 12 12" stroke="#fff" stroke-width="3" fill="none"/><path d="M27 8v8h-7" fill="#fff"/><rect x="10" y="14" width="10" height="7" fill="#fff"/><path d="M12 14v-3a3 3 0 0 1 6 0v3" stroke="#fff" stroke-width="2" fill="none"/></svg>
      <svg width="44" height="22" viewBox="0 0 44 22" aria-hidden="true"><rect x="1.5" y="1.5" width="37" height="19" rx="2" stroke="#fff" stroke-width="2.5" fill="none"/><rect x="5" y="5" width="30" height="12" fill="#fff"/><rect x="40" y="7" width="3" height="8" fill="#fff"/></svg>
    </div>
  </div>

  <header class="app-header">
    <svg class="header-back" width="22" height="38" viewBox="0 0 22 38" aria-label="Back"><path d="M19 3 4 19l15 16" stroke="#fff" stroke-width="4" fill="none"/></svg>
    <h1 class="app-title">Kest Apps</h1>
    <svg class="header-menu" width="42" height="28" viewBox="0 0 42 28" aria-label="Menu"><rect y="0" width="42" height="4" fill="#fff"/><rect y="12" width="42" height="4" fill="#fff"/><rect y="24" width="42" height="4" fill="#fff"/></svg>
  </header>

  <div class="question-bar">
    <span class="question-counter">QUESTION 7 OF 100</span>
    <svg class="question-next" width="16" height="30" viewBox="0 0 16 30" aria-label="Next question"><path d="M2 2l12 13L2 28" stroke="#1fbf3a" stroke-width="2.5" fill="none"/></svg>
  </div>

  <div class="content-backdrop" role="img" aria-label="Blurred background photo of a smiling family with a dog"></div>

  <div class="question-badge">?</div>
  <p class="question-bubble">A patient presents to the emergency room with the follow-ing symptoms: Anxiety, dyspnea, rhonchi, fever,Oxygen saturation of 88%, and a pH of 7.21. The nurse realized that the patient suffering from:</p>

  <ul class="answer-list">
    <li class="answer-option">A. Respiratory alkalosis</li>
    <li class="answer-option">B. Metabolic alkalosis</li>
    <li class="answer-option">C. Respiratory acidosis</li>
    <li class="answer-option">D. Metabolic acidosis</li>
  </ul>

  <div class="action-button confidence-button">CONFIDENCE</div>

  <svg class="confidence-slider" width="540" height="70" viewBox="0 0 540 70" aria-label="Confidence slider">
    <defs>
      <linearGradient id="track-fill" x1="0" y1="0" x2="0" y2="1"><stop offset="0" stop-color="#d8d8d8"/><stop offset="1" stop-color="#8a8a8a"/></linearGradient>
    </defs>
    <circle cx="13" cy="24" r="12" fill="#e0202a"/><rect x="6" y="22" width="14" height="4" fill="#fff"/>
    <circle cx="515" cy="24" r="12" fill="#1fbf3a"/><rect x="508" y="22" width="14" height="4" fill="#fff"/><rect x="513" y="17" width="4" height="14" fill="#fff"/>
    <rect x="58" y="16" width="415" height="16" rx="8" fill="url(#track-fill)" stroke="#777" stroke-width="1"/>
    <g stroke="#cfcfcf" stroke-width="1.5">
      <line x1="102" y1="36" x2="102" y2="54"/><line x1="144" y1="36" x2="144" y2="54"/><line x1="186" y1="36" x2="186" y2="54"/>
      <line x1="228" y1="36" x2="228" y2="54"/><line x1="270" y1="36" x2="270" y2="54"/><line x1="312" y1="36" x2="312" y2="54"/>
      <line x1="354" y1="36" x2="354" y2="54"/><line x1="396" y1="36" x2="396" y2="54"/><line x1="438" y1="36" x2="438" y2="54"/>
    </g>
    <path d="M258 8h16v24l-8 8-8-8z" fill="#ececec" stroke="#888" stroke-width="1.2"/>
  </svg>

  <div class="action-button submit-button">SUBMIT</div>
</div>
</body>
</html>
```